I need new business cards designed

I would like to get some new designs on business cards. I will upload my logo for reference. The business cards that were designed for me a few months ago were too difficult for the print companies to work with. My company is Quillbrook.net LLC. It is an art company that sells painting and expression cards online.

```html
<!DOCTYPE html>
<html lang="en">
<head>
<meta charset="utf-8">
<title>Quillbrook.net – Business Cards</title>
<link rel="stylesheet" href="https://fonts.googleapis.com/css2?family=Open+Sans:wght@400;600;700&display=swap">
<style>
  :root {
    --stage: #4a4a4a;
    --card: #161616;
    --edge: #00a0dc;
    --navy: #35367f;
    --sky: #00a0dc;
    --orange: #f7941d;
    --white: #f2f2f2;
  }
  * { box-sizing: border-box; margin: 0; padding: 0; }
  html, body {
    width: 1200px; height: 801px; overflow: hidden;
    background: var(--stage);
    font-family: "Open Sans", sans-serif;
  }
  .sheet {
    width: 1200px; height: 801px;
    display: flex; align-items: center; justify-content: center; gap: 40px;
  }
  .card {
    position: relative;
    width: 540px; height: 320px;
    background: var(--card);
    border-radius: 16px;
    border-left: 4px solid var(--edge);
    border-bottom: 4px solid var(--edge);
    box-shadow: 0 14px 30px rgba(0,0,0,.35);
    overflow: hidden;
  }

  /* brand block */
  .brand-name { color: var(--navy); font-weight: 400; line-height: 1; }
  .tagline { color: var(--sky); font-weight: 400; line-height: 1.1; }
  .brand-square { background: var(--orange); flex: none; }

  /* front card */
  .front .brand {
    position: absolute; left: 22px; top: 22px;
    display: flex; align-items: center; gap: 10px;
  }
  .front .brand .brand-square { width: 34px; height: 34px; }
  .front .brand .brand-name { font-size: 21px; }
  .front .brand .tagline { font-size: 11px; margin-top: 3px; }

  .front .accent-bar {
    position: absolute; right: 0; top: 118px;
    width: 44px; height: 16px; background: var(--sky);
  }
  .person {
    position: absolute; right: 64px; top: 136px; text-align: right;
  }
  .person .name {
    color: var(--sky); font-weight: 700; font-size: 23px;
    letter-spacing: .5px; line-height: 1.05;
  }
  .person .role { color: var(--white); font-size: 12px; margin-top: 2px; }
  .divider {
    position: absolute; left: 96px; right: 206px; top: 196px;
    height: 1px; background: var(--sky);
  }
  .address {
    position: absolute; right: 40px; top: 214px;
    color: var(--white); font-size: 12px; line-height: 1.45; text-align: right;
  }
  .socials {
    position: absolute; left: 300px; top: 262px;
    display: flex; gap: 10px;
  }
  .socials span {
    width: 13px; height: 13px; border-radius: 50%; background: var(--sky);
  }
  .contacts {
    position: absolute; left: 34px; bottom: 22px;
    list-style: none; color: var(--white); font-size: 12.5px;
  }
  .contacts li { display: flex; align-items: center; gap: 8px; line-height: 1.6; }
  .contacts svg { width: 13px; height: 13px; fill: var(--sky); flex: none; }

  /* back card */
  .back .brand {
    position: absolute; left: 50px; top: 50%; transform: translateY(-50%);
    display: flex; align-items: center; gap: 20px;
  }
  .back .brand .brand-square { width: 110px; height: 110px; }
  .back .brand .brand-name { font-size: 42px; }
  .back .brand .tagline { font-size: 18px; margin-top: 6px; }
</style>
</head>
<body>
<main class="sheet">

  <section class="card front" aria-label="Card front">
    <div class="brand">
      <div class="brand-square"></div>
      <div>
        <p class="brand-name">Quillbrook.net</p>
        <p class="tagline">Painting &amp; Expression Cards</p>
      </div>
    </div>

    <div class="accent-bar"></div>

    <div class="person">
      <p class="name">ELENA MARSH</p>
      <p class="role">Managing Director</p>
    </div>
    <div class="divider"></div>

    <p class="address">Your address, City<br>State, Zip 1234</p>

    <div class="socials" aria-hidden="true"><span></span><span></span><span></span></div>

    <ul class="contacts">
      <li><svg viewBox="0 0 16 16"><path d="M3.6 1.2l2.3 2.6-1.2 1.8c.8 1.9 2.3 3.4 4.2 4.3l1.8-1.2 2.6 2.3-1.5 2.6C6.8 13.3 2.6 9.1 1 4.2z"/></svg>555-318-2046</li>
      <li><svg viewBox="0 0 16 16"><path d="M1 3h14v10H1z M1.8 3.6L8 8.6l6.2-5" fill="none" stroke="#00a0dc" stroke-width="1.6"/></svg>hello@quillbrook.net</li>
      <li><svg viewBox="0 0 16 16"><circle cx="8" cy="8" r="6.5" fill="none" stroke="#00a0dc" stroke-width="1.5"/><path d="M1.5 8h13M8 1.5c-3 3.5-3 9.5 0 13M8 1.5c3 3.5 3 9.5 0 13" fill="none" stroke="#00a0dc" stroke-width="1.2"/></svg>www.Quillbrook.net</li>
    </ul>
  </section>

  <section class="card back" aria-label="Card back">
    <div class="brand">
      <div class="brand-square"></div>
      <div>
        <p class="brand-name">Quillbrook.net</p>
        <p class="tagline">Painting &amp; Expression Cards</p>
      </div>
    </div>
  </section>

</main>
</body>
</html>
```